Meadowlight Soaps Business Card

The new business card design will incorporate my new logo components designed by one of your designers. Meadowlight Soaps creates high quality soaps and bath products. They would be suited for a Spa, Bed and Breakfast, Boutique environment. The look should be a white background.
Classy, soft and using the colour palet of the logo. The card will be two sided.

Reason: Need more time to make some changes and decide.

Target Market(s)

Looking to appeal to an upper end market. Spas, boutiques, independent gift stores, bridal salons, bed and breakfast, etc. I want the card to impart a sense of elegance, tranquility and Meadowlight. But also quality and value.

Industry/Entity Type

Business

Font styles to use
Sans Serif
Script

Requirements
Must have
• My logo on the front. But also on the back but faded out to allow written notes on the back.
On the front : Carol Pritchett
Owner/Creator
48 Fenwick Rd
Guelph, Ont N4K 2P9
519.402.6183
Creating Quality Handcrafted Soaps And Bath Products
Custom and Wholesale Orders Welcome
Www.meadowlightsoaps.ca
Www.facebook.com / MeadowlightSoapandBath
info@meadowlightsoaps.ca

```html
<!DOCTYPE html>
<html lang="en">
<head>
<meta charset="utf-8">
<title>Meadowlight Soaps – Business Card</title>
<link rel="stylesheet" href="https://fonts.googleapis.com/css2?family=Jura:wght@500;600&display=swap">
<style>
  :root {
    --backdrop: #e9e7e4;
    --card-top: #fbfbfb;
    --card-bottom: #e6e7e7;
    --teal: #86b5aa;
    --teal-deep: #6fa396;
    --blush: #f1dccd;
    --ink: #2c2c2c;
    --ink-soft: #444;
    --rule: #3a3a3a;
  }
  html, body {
    margin: 0;
    width: 1200px;
    height: 899px;
    overflow: hidden;
    background: var(--backdrop);
    font-family: "Jura", sans-serif;
  }
  .card {
    position: absolute;
    left: 120px;
    top: 170px;
    width: 960px;
    height: 560px;
    border-radius: 56px;
    overflow: hidden;
    background: linear-gradient(160deg, var(--card-top) 0%, var(--card-bottom) 100%);
    box-shadow: 0 10px 30px rgba(0,0,0,0.12);
  }
  .card-wave {
    position: absolute;
    inset: 0;
  }
  .brand {
    position: absolute;
    left: 70px;
    top: 130px;
    width: 300px;
    text-align: center;
  }
  .brand-dot {
    width: 34px;
    height: 34px;
    border-radius: 50%;
    background: var(--teal);
    margin: 0 auto 18px;
  }
  .brand-name {
    font-size: 34px;
    font-weight: 500;
    color: var(--teal-deep);
    letter-spacing: 1px;
    line-height: 1.15;
  }
  .divider {
    position: absolute;
    left: 420px;
    top: 70px;
    width: 3px;
    height: 350px;
    background: var(--rule);
  }
  .details {
    position: absolute;
    left: 462px;
    top: 78px;
    color: var(--ink);
  }
  .person-name {
    font-size: 27px;
    font-weight: 600;
    letter-spacing: 2px;
    margin: 0;
  }
  .person-role {
    font-size: 22px;
    font-weight: 600;
    margin: 2px 0 0 8px;
  }
  .address {
    font-size: 21px;
    font-weight: 500;
    margin: 34px 0 0 8px;
    line-height: 1.35;
  }
  .contacts {
    list-style: none;
    margin: 28px 0 0 0;
    padding: 0;
    font-size: 17px;
    font-weight: 600;
    color: var(--ink-soft);
  }
  .contacts li {
    display: flex;
    align-items: center;
    gap: 12px;
    height: 31px;
  }
  .contacts svg {
    width: 16px;
    height: 16px;
    fill: var(--ink-soft);
    flex: none;
  }
</style>
</head>
<body>
  <div class="card">
    <svg class="card-wave" viewBox="0 0 960 560" preserveAspectRatio="none" aria-hidden="true">
      <path d="M0,318 C150,288 260,428 480,452 S820,478 960,496 L960,560 L0,560 Z" fill="var(--blush)"/>
      <path d="M0,340 C150,310 260,450 480,474 S820,500 960,518 L960,560 L0,560 Z" fill="var(--teal)"/>
    </svg>

    <div class="brand">
      <div class="brand-dot"></div>
      <div class="brand-name">Meadowlight Soaps</div>
    </div>

    <div class="divider"></div>

    <div class="details">
      <p class="person-name">MILES ARDENT</p>
      <p class="person-role">Managing Director</p>
      <p class="address">27 Larkspur Ave,Suite 4<br>Halden Park Road</p>
      <ul class="contacts">
        <li>
          <svg viewBox="0 0 16 16"><path d="M3 1l3 3-1.5 2a9 9 0 0 0 5.5 5.5L12 10l3 3-2 2C6 15 1 10 1 3z"/></svg>
          555 210 4418
        </li>
        <li>
          <svg viewBox="0 0 16 16"><path d="M4 0h8a1 1 0 0 1 1 1v14a1 1 0 0 1-1 1H4a1 1 0 0 1-1-1V1a1 1 0 0 1 1-1zm1 2v10h6V2zm3 11a1 1 0 1 0 0 2 1 1 0 0 0 0-2z"/></svg>
          555 377 9025
        </li>
        <li>
          <svg viewBox="0 0 16 16"><path d="M4 0h6v5H4zM1 6h14v9H1zm3 3v2h3V9zm5 0v2h3V9z"/></svg>
          555 210 4490
        </li>
        <li>
          <svg viewBox="0 0 16 16"><path d="M0 3h16v1L8 9 0 4zm0 3l8 5 8-5v7H0z"/></svg>
          hello@ardentmail.com
        </li>
        <li>
          <svg viewBox="0 0 16 16"><path d="M8 0a8 8 0 1 0 0 16A8 8 0 0 0 8 0zm0 2c1 1 1.8 3 2 5H6c.2-2 1-4 2-5zM2.1 7A6 6 0 0 1 5.3 2.6 10 10 0 0 0 4 7zm0 2H4a10 10 0 0 0 1.3 4.4A6 6 0 0 1 2.1 9zM6 9h4c-.2 2-1 4-2 5-1-1-1.8-3-2-5zm4.7 4.4A10 10 0 0 0 12 9h1.9a6 6 0 0 1-3.2 4.4zM12 7a10 10 0 0 0-1.3-4.4A6 6 0 0 1 13.9 7z"/></svg>
          www.milesardent.com
        </li>
      </ul>
    </div>
  </div>
</body>
</html>
```